Envelope Design - Winner can do follow-up business

- Varnoko.com is a Swiss-based online store selling business shirts and accessories for business men
- Please visit the webpage to make yourself familiar with the company. Although the text is in German, with Plimbo translator you should be able to understand the main content.
- Our clients are mainly business men between 30 and 60 years old. Mostly with a high income working in the service industry (banking, insurance, lawyers, etc.). Sometimes there wives purchase the shirts for them ;-)
- The colors and the logo are given, as they are also used for the print materials (please see files in attachment)
- I am running several businesses and often need a talented web designer --> the winner gets substantial follow-up business
your task:
-for our company we need a new envelope design
-It should be simple and modern
-please use one of the logos in the followings.
-suprise me :)

```html
<!DOCTYPE html>
<html lang="en">
<head>
<meta charset="utf-8">
<title>Varnoko Envelope Set</title>
<link rel="stylesheet" href="https://fonts.googleapis.com/css2?family=Krona+One&family=Open+Sans:wght@400&display=swap">
<style>
  :root {
    --backdrop: #ebe8e4;
    --paper: #ffffff;
    --brand-red: #ef3024;
    --brand-red-soft: #f24e2c;
    --brand-yellow: #e8d76a;
    --ink: #1f1f1f;
    --edge: #9a9a9a;
    --ghost: #fdf2e4;
  }
  * { box-sizing: border-box; margin: 0; padding: 0; }
  html, body { width: 1200px; height: 941px; overflow: hidden; }
  body { background: var(--backdrop); position: relative; font-family: "Open Sans", Arial, sans-serif; }

  .envelope {
    position: absolute;
    width: 1011px;
    background: var(--paper);
    box-shadow: 0 2px 6px rgba(0,0,0,0.18);
  }
  .envelope--back   { left: 142px; top: 54px;  height: 477px; }
  .envelope--middle { left: 48px;  top: 232px; height: 476px; border-right: 1px solid var(--edge); }
  .envelope--front  { left: 85px;  top: 410px; height: 475px; }

  .envelope__flap { position: absolute; left: 0; top: 0; width: 1011px; height: 162px; display: block; }
  .envelope__top-rule { position: absolute; left: 0; top: 0; width: 100%; height: 5px; }
  .envelope--back .envelope__top-rule { background: var(--brand-red); }
  .envelope--middle .envelope__top-rule { background: #000; }
  .envelope--front .envelope__top-rule { background: var(--brand-yellow); }

  .wordmark {
    position: absolute;
    font-family: "Krona One", "Arial Black", sans-serif;
    font-weight: 400;
    line-height: 1;
    white-space: nowrap;
  }
  .wordmark--flap { left: 0; width: 100%; top: 52px; text-align: center; font-size: 38px; color: var(--brand-red); letter-spacing: 1px; }
  .wordmark--flap-soft { left: 0; width: 100%; top: 48px; text-align: center; font-size: 30px; color: var(--brand-red-soft); letter-spacing: 1px; }

  .sender { position: absolute; left: 31px; top: 36px; }
  .sender__square { width: 40px; height: 40px; background: var(--brand-yellow); margin-left: 108px; }
  .wordmark--sender { position: static; display: block; margin-top: 22px; font-size: 38px; color: var(--brand-yellow); letter-spacing: 1px; }

  .ghost-square { position: absolute; left: 828px; top: 272px; width: 168px; height: 168px; background: var(--ghost); }

  .contact { position: absolute; left: 26px; bottom: 16px; display: flex; align-items: center; gap: 36px; font-size: 20px; color: var(--ink); }
  .contact__item { display: flex; align-items: center; gap: 10px; }
  .contact__icon { width: 24px; height: 24px; flex: none; }
</style>
</head>
<body>

  <section class="envelope envelope--back" aria-label="Envelope with yellow flap">
    <svg class="envelope__flap" viewBox="0 0 1011 162" preserveAspectRatio="none" aria-hidden="true">
      <path d="M0,0 H1011 C1000,45 990,75 940,84 L540,155 Q505,162 470,155 L70,84 C20,75 10,45 0,0 Z" fill="var(--brand-yellow)"/>
    </svg>
    <div class="envelope__top-rule"></div>
    <span class="wordmark wordmark--flap">VARNOKO</span>
  </section>

  <section class="envelope envelope--middle" aria-label="Envelope with red flap">
    <svg class="envelope__flap" viewBox="0 0 1011 162" preserveAspectRatio="none" aria-hidden="true">
      <path d="M0,0 H1011 C1000,45 990,75 940,84 L540,155 Q505,162 470,155 L70,84 C20,75 10,45 0,0 Z" fill="var(--brand-red)"/>
    </svg>
    <div class="envelope__top-rule"></div>
    <span class="wordmark wordmark--flap-soft">VARNOKO</span>
  </section>

  <section class="envelope envelope--front" aria-label="Envelope front">
    <div class="envelope__top-rule"></div>
    <div class="sender">
      <div class="sender__square"></div>
      <span class="wordmark wordmark--sender">VARNOKO</span>
    </div>
    <div class="ghost-square"></div>
    <div class="contact">
      <span class="contact__item">
        <svg class="contact__icon" viewBox="0 0 24 24" aria-hidden="true">
          <path d="M12 1C7.6 1 4.5 4.3 4.5 8.5 4.5 14 12 23 12 23s7.5-9 7.5-14.5C19.5 4.3 16.4 1 12 1z" fill="var(--brand-red)"/>
          <circle cx="12" cy="8.5" r="3" fill="#fff"/>
        </svg>
        Street Name, City Name, State Zipcode
      </span>
      <span class="contact__item">
        <svg class="contact__icon" viewBox="0 0 24 24" aria-hidden="true" fill="none" stroke="var(--brand-red)" stroke-width="1.5">
          <circle cx="12" cy="12" r="10"/>
          <ellipse cx="12" cy="12" rx="4.5" ry="10"/>
          <path d="M2 12h20M3.5 7h17M3.5 17h17M12 2v20"/>
        </svg>
        www.varnoko.com
      </span>
    </div>
  </section>

</body>
</html>
```